Natural Australian skin care company packaging for new product Bath salts

We are moving to fully refillable packaging and need someone to design our refill pouches. we have a number of products we need to do this for but our first one is our natural bath salts. This comes in a 200g tin in a pouch then the pouch can be bought to refill the tin. We can either print on the pouch or do sickers. The tin is a simple matt black tin with white text on the lid. the pouch comes in a gold colour. pictures are in the drop box lid.
Luxury bath salts Pouch - the dimensions are 60*55*180mm, , we can either print directly or do a sticker, We also need the sleeve to go around the tin. The dimensions of the tin are 65x65x70mm. The same text needs to go onto the sleeve as the pouch. The tin is black with white printing on the top (see picture).
Text is as follows
MB logo Calm reed drift 100% pure magnesium bath salts
A rich fragrance of Australian wild flowers (using natural essential oils) with frangipani and gardenia. Sink into the natural ancient salt lake sourced 100% pure magnesium to replenish your skin. Transdermal absorption of magnesium is effective and contributes to electrolyte balance, normal muscle function and aids calcium absorption. The ultimate mineral reset.
Directions: Fill bath, once full put two heaped tablespoons of the salts into the bath (approx 50g). Climb in and relax.
Menzo Balm full logo
Country of Origin: Australia
PO Box 318
Ellory Bay 4612
QLD Australia
www.menzobalm-example.com
ingredients:
magnesium chloride *, parfum **
*naturally sourced from ancient salt lakes
**a combination of essential oils and natural isolates.
e: 200g / 7.05 Oz
We also need the recycle, plastic free, not tested on animal eco friendly symbols.
Please use this link to our press assets and tin and pouch photos.
https://www.filecrate-example.com/sh/kq8vt341plmwx27/BBtoLw__qRsYYjmK-HuvgNeTa?dl=0

```html
<!DOCTYPE html>
<html lang="en">
<head>
<meta charset="utf-8">
<title>Menzo Balm – Magnesium Bath Salts Labels</title>
<link rel="stylesheet" href="https://fonts.googleapis.com/css2?family=Roboto+Slab:wght@300;400;600;700&display=swap">
<style>
  :root {
    --backdrop: #3b3b3d;
    --label: #ffffff;
    --pattern-tint: #f6f6f6;
    --ink: #111111;
    --icon-grey: #555555;
  }
  * { margin: 0; padding: 0; box-sizing: border-box; }
  html, body { width: 930px; height: 1200px; overflow: hidden; }
  body {
    background: var(--backdrop);
    font-family: "Roboto Slab", Georgia, serif;
    color: var(--ink);
    position: relative;
  }
  .label {
    position: absolute;
    top: 132px;
    width: 314px;
    height: 936px;
    background: var(--label);
    overflow: hidden;
  }
  .label--front { left: 132px; }
  .label--back { left: 485px; }
  .label__texture {
    position: absolute; inset: 0;
    background: linear-gradient(180deg, var(--pattern-tint), #fbfbfb);
  }
  .brand-mark {
    position: absolute;
    border-radius: 50%;
    background: var(--ink);
  }
  .brand-name {
    position: absolute; left: 0; width: 100%;
    text-align: center;
    font-weight: 600;
    letter-spacing: 1px;
    text-transform: uppercase;
  }
  .brand-tagline {
    position: absolute; left: 0; width: 100%;
    text-align: center;
    font-size: 6.5px;
    letter-spacing: 0.6px;
    text-transform: uppercase;
  }
  .front-art { position: absolute; left: 0; top: 0; }
  .net-weight {
    position: absolute; left: 0; width: 100%; top: 868px;
    text-align: center; font-size: 15px;
  }
  .copy {
    position: absolute; left: 0; width: 100%;
    text-align: center;
    font-size: 9.4px;
    line-height: 14.6px;
  }
  .eco-icons { position: absolute; left: 0; top: 836px; }
</style>
</head>
<body>

  <section class="label label--front" aria-label="Front label">
    <div class="label__texture" role="img" aria-label="Faint repeating brand monogram background"></div>
    <div class="brand-mark" style="left:114px; top:336px; width:80px; height:80px;"></div>
    <div class="brand-name" style="top:452px; font-size:20px;">Menzo Balm</div>
    <div class="brand-tagline" style="top:484px;">Australian Bush Medicines</div>

    <svg class="front-art" width="314" height="936" viewBox="0 0 314 936">
      <g stroke="var(--ink)" stroke-width="2">
        <line x1="56" y1="502" x2="252" y2="502"/>
        <line x1="56" y1="860" x2="252" y2="860"/>
        <line x1="57" y1="502" x2="57" y2="860"/>
      </g>
      <g fill="var(--ink)" font-family="Roboto Slab, Georgia, serif" text-transform="uppercase">
        <text transform="translate(86 856) rotate(-90)" font-size="33" font-weight="300" textLength="340" lengthAdjust="spacingAndGlyphs">CALM REED DRIFT</text>
        <text transform="translate(144 856) rotate(-90)" font-size="62" font-weight="700" textLength="340" lengthAdjust="spacingAndGlyphs">100% PURE</text>
        <text transform="translate(200 856) rotate(-90)" font-size="62" font-weight="700" textLength="340" lengthAdjust="spacingAndGlyphs">MAGNESIUM</text>
        <text transform="translate(252 856) rotate(-90)" font-size="62" font-weight="700" textLength="340" lengthAdjust="spacingAndGlyphs">BATH SALTS</text>
      </g>
    </svg>

    <div class="net-weight">200g / 7.05 Oz</div>
  </section>

  <section class="label label--back" aria-label="Back label">
    <div class="label__texture" role="img" aria-label="Faint repeating brand monogram background"></div>
    <div class="brand-mark" style="left:121px; top:394px; width:70px; height:70px;"></div>
    <div class="brand-name" style="top:473px; font-size:18px;">Menzo Balm</div>
    <div class="brand-tagline" style="top:500px;">Australian Bush Medicines</div>

    <p class="copy copy--description" style="top:520px;">
      A rich fragrance of Australian wild flowers (using<br>
      natural essential oils) with frangipani and gardenia.<br>
      Sink into the natural ancient salt lake sourced 100%<br>
      pure magnesium to replenish your skin. Transdermal<br>
      absorption of magnesium is effective and contributes<br>
      to electrolyte balance, normal muscle function and<br>
      aids calcium absorption. The ultimate mineral reset.
    </p>

    <p class="copy copy--directions" style="top:627px;">
      DIRECTIONS:<br>
      Fill bath, once full put two heaped tablespoons<br>
      of the salts into the bath (approx 50g).<br>
      Climb in and relax.
    </p>

    <p class="copy copy--ingredients" style="top:693px;">
      INGREDIENTS:<br>
      Magnesium chloride *, Parfum *<br>
      <br>
      *naturally sourced from ancient salt lakes<br>
      **a combination of essential oils and natural isolates.
    </p>

    <p class="copy copy--address" style="top:777px;">
      PO Box 318<br>
      Ellory Bay 4612, QLD Australia<br>
      www.menzobalm-example.com
    </p>

    <svg class="eco-icons" width="314" height="56" viewBox="0 0 314 56" aria-label="Eco symbols: recyclable, not tested on animals, plastic free, eco friendly">
      <g fill="none" stroke="var(--icon-grey)" stroke-width="2">
        <path d="M64 10 L82 42 L46 42 Z" stroke-width="5" stroke-linejoin="round"/>
        <circle cx="129" cy="28" r="23"/>
        <circle cx="192" cy="28" r="23"/>
        <circle cx="255" cy="28" r="21"/>
      </g>
    </svg>
  </section>

</body>
</html>
```